creation of a business card design for a company specializing in the creation...

I would like to create a design for a professional business card on a black background and with the company's colors (I am attaching some files: including the logo in horizontal and centered format, I am also attaching a recent project design a T-shirt, this is the one I chose to give you an idea of my preferences.

we are in the process of developing a new website design, it is still in the development phase but it can be viewed at the following address: www.vantrelmo.be to give you other ideas about the company
you will see for yourself the subject of my main activity: company specializing in the construction of stairs

I would like a business card that stands out from the rest with a unique design

here is the informations
Name: Lucien Barthel
Function: Manager
Address: Rue Moulinet du Parc 42
7180 La Louvière
telephone: +32 468 219 804
email: info@rx7p.be
website: rx7p. be
social networks: Facebook, YouTube, TikTok, Instagram

Target Market(s)

customer who wants to have a beautiful staircase built

Industry/Entity Type

contruction d'escalier

Contact Information for Business Card

Adresse. Numero de telephone, site web, le texte : "Createur d'escalier", logo recto-verso, icone des reseaux sociaux

Requirements
Must have
• the mention: Stair creator
Nice to have
• an illustration of a designer staircase
Should not have
• do not distort the logo

```html
<!DOCTYPE html>
<html lang="en">
<head>
<meta charset="utf-8">
<title>RX7P Business Card</title>
<link href="https://fonts.googleapis.com/css2?family=Montserrat:wght@400;500;600;700&display=swap" rel="stylesheet">
<style>
  :root {
    --bg: #2a2a2d;
    --card: #232323;
    --accent: #7fa9c9;
    --text: #f2f2f2;
    --muted: #d8d8d8;
  }
  * { margin: 0; padding: 0; box-sizing: border-box; }
  html, body { width: 1200px; height: 900px; overflow: hidden; }
  body {
    background: var(--bg);
    font-family: "Montserrat", sans-serif;
    position: relative;
  }
  .card {
    position: absolute;
    left: 290px;
    width: 620px;
    height: 400px;
    background: var(--card);
    border-radius: 22px;
    box-shadow: 0 12px 30px rgba(0,0,0,0.35);
  }
  .card--back { top: 35px; }
  .card--front { top: 465px; }

  .brand {
    position: absolute;
    display: flex;
    align-items: center;
    gap: 22px;
  }
  .brand__mark {
    width: 64px;
    height: 64px;
    background: var(--accent);
    flex: none;
  }
  .brand__text { display: flex; flex-direction: column; }
  .brand__name {
    font-weight: 600;
    color: var(--text);
    letter-spacing: 6px;
    line-height: 1;
  }
  .brand__tagline {
    font-weight: 500;
    color: var(--accent);
    text-transform: uppercase;
    letter-spacing: 5px;
    margin-top: 10px;
    white-space: nowrap;
  }
  .card--back .brand { left: 50%; top: 50%; transform: translate(-50%, -50%); }
  .card--back .brand__name { font-size: 64px; }
  .card--back .brand__tagline { font-size: 12px; }
  .card--front .brand { right: 44px; top: 40px; gap: 18px; }
  .card--front .brand__mark { width: 54px; height: 54px; }
  .card--front .brand__name { font-size: 54px; }
  .card--front .brand__tagline { font-size: 11px; letter-spacing: 4.5px; }

  .holder { position: absolute; left: 48px; top: 150px; }
  .holder__name { color: var(--accent); font-weight: 700; font-size: 26px; }
  .holder__role { color: var(--text); font-size: 14px; font-weight: 500; margin-top: 2px; }

  .address {
    position: absolute; left: 48px; top: 232px;
    color: var(--muted); font-size: 14px; line-height: 1.35;
  }
  .contacts {
    position: absolute; left: 48px; top: 285px;
    list-style: none; font-size: 14px; color: var(--muted);
  }
  .contacts li { display: flex; align-items: center; gap: 10px; height: 20px; }
  .contacts svg { width: 14px; height: 14px; fill: var(--accent); }
  .social {
    position: absolute; left: 48px; top: 352px;
    display: flex; align-items: center; gap: 9px;
    color: var(--muted); font-size: 14px;
  }
  .social__slot { width: 16px; height: 16px; border-radius: 3px; background: var(--accent); }
</style>
</head>
<body>
  <section class="card card--back">
    <div class="brand">
      <span class="brand__mark"></span>
      <div class="brand__text">
        <span class="brand__name">RX7P</span>
        <span class="brand__tagline">Original Staircases</span>
      </div>
    </div>
  </section>

  <section class="card card--front">
    <div class="brand">
      <span class="brand__mark"></span>
      <div class="brand__text">
        <span class="brand__name">RX7P</span>
        <span class="brand__tagline">Original Staircases</span>
      </div>
    </div>

    <div class="holder">
      <p class="holder__name">Lucien Barthel</p>
      <p class="holder__role">Manager</p>
    </div>

    <p class="address">Rue Moulinet du Parc 42<br>7180 La Louvière</p>

    <ul class="contacts">
      <li>
        <svg viewBox="0 0 24 24" aria-hidden="true"><path d="M6.6 10.8a15 15 0 0 0 6.6 6.6l2.2-2.2a1 1 0 0 1 1-.25 11.4 11.4 0 0 0 3.6.57 1 1 0 0 1 1 1V20a1 1 0 0 1-1 1A17 17 0 0 1 3 4a1 1 0 0 1 1-1h3.5a1 1 0 0 1 1 1c0 1.25.2 2.45.57 3.57a1 1 0 0 1-.25 1z"/></svg>
        +32 468 219 804
      </li>
      <li>
        <svg viewBox="0 0 24 24" aria-hidden="true"><path d="M2 5h20v14H2z M4 7v.5l8 5 8-5V7l-8 5z" fill-rule="evenodd"/></svg>
        info@rx7p.be
      </li>
      <li>
        <svg viewBox="0 0 24 24" aria-hidden="true"><path d="M12 2a10 10 0 1 0 0 20 10 10 0 0 0 0-20zm0 2c.9 1.2 1.6 2.9 1.9 5h-3.8c.3-2.1 1-3.8 1.9-5zM4.3 13h3.8c.1 1.8.4 3.4 1 4.7A8 8 0 0 1 4.3 13zm0-2a8 8 0 0 1 4.8-4.7c-.6 1.3-.9 2.9-1 4.7zm7.7 9c-.9-1.2-1.6-2.9-1.9-5h3.8c-.3 2.1-1 3.8-1.9 5zm2.9-2.3c.6-1.3.9-2.9 1-4.7h3.8a8 8 0 0 1-4.8 4.7zm1-6.7c-.1-1.8-.4-3.4-1-4.7a8 8 0 0 1 4.8 4.7z"/></svg>
        www.rx7p.be
      </li>
    </ul>

    <div class="social">
      <span class="social__slot" role="img" aria-label="Social network icon"></span>
      <span class="social__slot" role="img" aria-label="Social network icon"></span>
      <span class="social__slot" role="img" aria-label="Social network icon"></span>
      <span class="social__slot" role="img" aria-label="Social network icon"></span>
      <span>rx7p.be</span>
    </div>
  </section>
</body>
</html>
```